Heron Loan Partners Business Card

We need a business card design for our mortgage servicing company. In addition to servicing the loans of homeowners, we help homeowners with purchasing their homes and any mortgage refinancing. We would like to see designs that use the colors in the logo attached below (gold-ish yellow and navy blue), and any other design you deem fit! The design should communicate a simpler life with smart mortgages provided by Heron.

```html
<!DOCTYPE html>
<html lang="en">
<head>
<meta charset="utf-8">
<title>Heron Loan Partners Business Card</title>
<link href="https://fonts.googleapis.com/css2?family=Open+Sans:wght@400;600;700&display=swap" rel="stylesheet">
<style>
  :root {
    --gold: #e2b140;
    --navy: #261f59;
    --ink: #111111;
    --paper: #ffffff;
    --backdrop: #232323;
  }
  * { margin: 0; padding: 0; box-sizing: border-box; }
  html, body { width: 1200px; height: 780px; overflow: hidden; background: var(--backdrop); }
  body { font-family: "Open Sans", Arial, sans-serif; position: relative; }

  .card {
    position: absolute;
    top: 235px;
    width: 540px;
    height: 310px;
    border-radius: 22px;
    overflow: hidden;
    background: var(--paper);
    box-shadow: 0 14px 30px rgba(0,0,0,0.55);
  }
  .card--front { left: 40px; }
  .card--back { left: 620px; }

  .card__bands { position: absolute; inset: 0; width: 100%; height: 100%; }

  .brand {
    position: absolute;
    display: flex;
    align-items: center;
    gap: 10px;
    color: var(--navy);
    font-weight: 700;
    white-space: nowrap;
  }
  .brand__dot { border-radius: 50%; background: var(--gold); flex: none; }
  .card--front .brand { left: 0; right: 0; top: 132px; justify-content: center; font-size: 34px; }
  .card--front .brand__dot { width: 30px; height: 30px; }
  .card--back .brand { left: 60px; top: 138px; font-size: 17px; gap: 7px; }
  .card--back .brand__dot { width: 16px; height: 16px; }

  .divider {
    position: absolute;
    left: 262px;
    top: 62px;
    width: 1px;
    height: 160px;
    background: var(--ink);
  }

  .contact { position: absolute; left: 282px; top: 58px; }
  .contact__name { font-size: 25px; font-weight: 700; color: var(--ink); line-height: 1.1; }
  .contact__first { color: var(--gold); }
  .contact__title { font-size: 13px; font-weight: 600; color: var(--ink); margin-top: 2px; }
  .contact__list { list-style: none; margin-top: 12px; }
  .contact__item {
    display: flex; align-items: center; gap: 8px;
    font-size: 12.5px; color: var(--ink); line-height: 1.75;
  }
  .contact__icon { width: 13px; height: 13px; flex: none; }

  .address {
    position: absolute;
    left: 0; right: 0; bottom: 26px;
    text-align: center;
    font-size: 14px;
    color: var(--ink);
  }
</style>
</head>
<body>

  <section class="card card--front" aria-label="Business card front">
    <svg class="card__bands" viewBox="0 0 540 310" preserveAspectRatio="none" aria-hidden="true">
      <path d="M0 0 H150 C90 40 55 100 50 180 L0 180 Z" fill="var(--gold)"/>
      <path d="M540 310 H390 C460 280 505 220 510 120 L540 110 Z" fill="var(--navy)"/>
    </svg>
    <div class="brand"><span class="brand__dot"></span>Heron Loan Partners</div>
  </section>

  <section class="card card--back" aria-label="Business card back">
    <svg class="card__bands" viewBox="0 0 540 310" preserveAspectRatio="none" aria-hidden="true">
      <path d="M0 0 H130 C75 40 45 100 42 180 L0 180 Z" fill="var(--gold)"/>
      <path d="M540 310 H400 C465 280 505 220 512 125 L540 115 Z" fill="var(--navy)"/>
    </svg>

    <div class="brand"><span class="brand__dot"></span>Heron Loan Partners</div>
    <div class="divider"></div>

    <div class="contact">
      <p class="contact__name"><span class="contact__first">Lena</span> Marvik</p>
      <p class="contact__title">Managing Director</p>
      <ul class="contact__list">
        <li class="contact__item">
          <svg class="contact__icon" viewBox="0 0 16 16" aria-hidden="true"><path d="M3 1.5l3 .5 1 3-1.8 1.3a8 8 0 0 0 4.5 4.5L11 9l3 1 .5 3-2 1.5C7 14 2 9 1.5 3.5z" fill="var(--gold)"/></svg>
          (555) 204-3187
        </li>
        <li class="contact__item">
          <svg class="contact__icon" viewBox="0 0 16 16" aria-hidden="true"><rect x="1" y="3" width="14" height="10" rx="1.5" fill="var(--gold)"/><path d="M1.5 4l6.5 5 6.5-5" stroke="#fff" stroke-width="1.3" fill="none"/></svg>
          info@heronloan.com
        </li>
        <li class="contact__item">
          <svg class="contact__icon" viewBox="0 0 16 16" aria-hidden="true"><circle cx="8" cy="8" r="7" fill="var(--gold)"/><path d="M1 8h14M8 1c-3 3-3 11 0 14M8 1c3 3 3 11 0 14" stroke="#fff" stroke-width="1" fill="none"/></svg>
          www.heronloan.com
        </li>
      </ul>
    </div>

    <p class="address">1840 Willow Bend Rd. Suite 310 Cedar Falls, TX 75410</p>
  </section>

</body>
</html>
```